Innovative cost reduction consultant needs to build a group of technical advisors

We need to share our message and compassion for developing cost reduction in the automotive industry. We create opportunities for immediate innovation, by developing cost reduction solutions across suppliers with related process. Attached is an existing Power Point, but it needs improvement. Most of all, a good compelling story, why experts should join us.

Target Market(s)

Automotive industry, supply chain management

Industry/Entity Type

Automotive

Font styles to use
Serif
Sans Serif

Requirements
Must have
• Better visual graphics. There are a few, but they are not as visually appearing as I would like. A graphic with data should have a better visual impact then the ones that I created. I would like to share the message, that I am providing a solution for the automotive industry. The goal is to reduce costs and improve supplier and OEM relationships. The objective is to do so by creating opportunities for immediate innovation, by developing cost reduction solutions across suppliers with related processes. This message may need a visual graphic, which is missing from the presentation.
Nice to have
• Challenge my story and presentation. Does this make sense to you, and what is your opinions of the subject. Or, a relevant news source to validate the story.
Should not have
• I have not decided on the name of the venture or logo. So, let's just use my name as the source or writer. Marcus Delby, Cost Reduction Specialist. Thanks,

```html
<!DOCTYPE html>
<html lang="en">
<head>
<meta charset="utf-8">
<title>Creating Opportunities For Immediate Innovation – Marcus Delby</title>
<link href="https://fonts.googleapis.com/css2?family=Raleway:ital,wght@0,300;0,400;0,600;0,700;1,400&family=Libre+Baskerville:wght@400;700&family=Montserrat:wght@600;700&display=swap" rel="stylesheet">
<style>
:root{
  --navy:#1b2f6b;
  --navy-deep:#13225a;
  --navy-light:#2a4286;
  --ink:#16204a;
  --red:#c8382f;
  --white:#ffffff;
  --steel-a:#8d929a;
  --steel-b:#2c2f36;
  --cell-red:#e8675a;
  --cell-orange:#f3a35b;
  --cell-yellow:#f6dc74;
  --cell-green:#69b86d;
  --cell-pale:#fbeec6;
}
*{box-sizing:border-box;margin:0;padding:0}
html,body{width:855px;height:1200px;overflow:hidden;background:var(--white)}
body{position:relative;font-family:"Raleway",sans-serif;color:var(--white)}
.slide{position:absolute;width:409px;height:230px;overflow:hidden;background:var(--navy);box-shadow:0 1px 4px rgba(0,0,0,.35)}
.col-a{left:11px}.col-b{left:436px}
.row-1{top:5px}.row-2{top:245px}.row-3{top:485px}.row-4{top:725px}.row-5{top:965px}
.abs{position:absolute}
.nowrap{white-space:nowrap}
.page-no{position:absolute;right:20px;bottom:6px;font-size:5px;color:#9aa4c4}
.photo-gears{background:radial-gradient(circle at 30% 60%,var(--steel-a),var(--steel-b) 70%)}
.photo-sparks{background:radial-gradient(circle at 80% 40%,#f4d9a8 0,#8a6a48 18%,#1d2232 55%)}
.header-band{position:absolute;left:0;top:0;height:38px;background:var(--white);color:var(--ink);font-weight:300;font-size:16px;display:flex;align-items:center;gap:6px;padding-left:3px;white-space:nowrap}
.bar{display:inline-block;width:8px;height:14px;border-left:3px solid var(--navy);border-right:3px solid var(--navy);flex:none}
.bar-light{position:absolute;width:8px;height:13px;border-left:3px solid #fff;border-right:3px solid #fff}
.dark-title{position:absolute;left:18px;font-size:15px;line-height:16.5px;font-weight:300}
.panel{position:absolute;background:var(--navy)}
.tick{display:inline-block;width:9px;height:9px;vertical-align:-1px;margin-right:4px}
.cover-photo{position:absolute;inset:0;clip-path:polygon(0 0,58% 0,36% 100%,0 100%);background:linear-gradient(135deg,#7d1f1a 0,var(--red) 30%,#e8e3df 62%,#bfb9b4 100%)}
.cover-title{position:absolute;right:9px;top:84px;text-align:right;font-size:11.5px;line-height:14.5px;font-weight:300;white-space:nowrap}
.cover-title b{font-weight:700}
.cover-byline{position:absolute;right:9px;top:187px;font-size:5.6px;font-weight:700}
.cover-date{position:absolute;right:9px;top:203px;font-size:5.6px}
.sunset{position:absolute;inset:0;background:linear-gradient(180deg,#1b2f6b 0,#36427a 35%,#c77d3c 68%,#2a1e1c 100%)}
.news{position:absolute;left:10px;top:15px;width:264px;height:205px;background:var(--white);color:#222;padding:6px 7px;font-family:"Libre Baskerville",serif;overflow:hidden}
.news-mast{font-size:19px;font-weight:700;color:var(--navy-deep);letter-spacing:-.5px}
.news-head{font-family:"Raleway",sans-serif;font-size:5px;font-weight:700;color:var(--navy);margin:3px 0 6px}
.news-meta{font-size:3.6px;color:#555;line-height:5px;margin-bottom:5px}
.news-body{font-size:3.7px;line-height:4.8px}
.news-body p{margin-bottom:3px}
.news-side{position:absolute;left:277px;top:54px;width:106px;font-size:9.5px;line-height:12px;font-style:italic;font-weight:400}
.news-side p{margin-bottom:10px}
.grid-svg text{font-family:"Raleway",sans-serif}
.small{font-size:7px;line-height:9px}
.node{position:absolute;border:1px solid var(--white);font-size:5.5px;text-align:center;padding:2px}
.pill{position:absolute;background:var(--white);color:var(--navy);font-size:5.5px;padding:3px 6px;border-radius:2px}
.quad{position:absolute;left:79px;top:114px;width:251px;height:74px;border:1px solid var(--white);border-radius:6px}
.quad span{position:absolute;font-size:7.5px;width:50%;text-align:center}
.impact{position:absolute;left:158px;top:143px;width:93px;height:17px;background:var(--navy-light);border:1px solid var(--white);border-radius:3px;font-size:7.5px;text-align:center;line-height:15px}
.center-label{position:absolute;text-align:center;transform:translate(-50%,-50%);white-space:nowrap}
</style>
</head>
<body>

<!-- 1 Cover -->
<section class="slide col-a row-1">
  <div class="cover-photo" role="img" aria-label="Photo of scissors cutting a red sheet of paper marked with the word cost"></div>
  <div class="cover-title"><b>Creating Opportunities For<br>Immediate Innovation,</b><br>By Developing Cost Reduction<br>Solutions Across Suppliers With<br>Related Processes.</div>
  <div class="cover-byline">By Marcus Delby, Cost Reduction Specialist</div>
  <div class="cover-date">December 2<sup>nd</sup>, 2016</div>
</section>

<!-- 2 News -->
<section class="slide col-b row-1">
  <div class="sunset" role="img" aria-label="Photo of a sunset over an industrial skyline"></div>
  <article class="news">
    <div class="news-mast">Motor Trade Weekly</div>
    <div class="news-head">Automakers' efforts to cut costs damages supplier relations, survey says</div>
    <div class="news-meta">Evan Porter<br>Motor Trade Weekly | December 22, 2014 · 12:01 am EST</div>
    <div class="news-body">
      <p><b>Relations between automakers and suppliers are deteriorating largely because of intensifying cost-cutting demands, according to a survey.</b></p>
      <p>Relations between automakers and suppliers are deteriorating largely because of intensifying cost-cutting demands, according to a new survey.</p>
      <p>Vehicle manufacturers are looking for annual price reductions of as much as 10 percent, parts makers revealed in the 2014 Global OEM-Supplier Relations Study conducted by consultant Meridian Research.</p>
      <p>"With few exceptions, even the best performing carmakers have become more stringent on controlling costs in 2014, signaling a general shift toward cost focus and more aggressive ways to use their negotiation leverage," said Luca Ventri, the study's lead author.</p>
      <p>The standard annual price reduction by automakers is about 2 to 3 percent, but cuts of 5 percent or more are not uncommon.</p>
      <p>"Suppliers seem to accept that they have to find innovative ways to generate savings, yet they receive little or no support from the OEMs in doing so," Ventri wrote.</p>
    </div>
  </article>
  <div class="news-side">
    <p>Increasing pressure to reduce costs has created a strain on supplier relations.</p>
    <p>Suppliers are left alone with very little or no support from the OEM</p>
  </div>
  <div class="page-no">2</div>
</section>

<!-- 3 Case study -->
<section class="slide col-a row-2">
  <div class="abs photo-gears" style="inset:0" role="img" aria-label="Photo of steel industrial gears"></div>
  <div class="panel" style="left:0;top:38px;width:409px;height:163px"></div>
  <div class="header-band" style="width:220px;clip-path:polygon(0 0,100% 0,92% 100%,0 100%)"><span class="bar"></span>Case Study…</div>
  <div class="abs" style="left:45px;top:70px;width:128px;height:83px;background:linear-gradient(135deg,#f2f4f8,#c7d7ec 40%,#f1d27a 60%,#e88b8b 80%,#d9e9d2)" role="img" aria-label="Map of North American supplier locations by region"></div>
  <div class="abs small" style="right:14px;top:55px;text-align:right;width:200px">
    <p style="margin-bottom:9px"><svg class="tick" viewBox="0 0 10 10"><circle cx="5" cy="5" r="5" fill="#fff"/><path d="M2.6 5.2 4.3 6.8 7.4 3.5" stroke="#1b2f6b" stroke-width="1.3" fill="none"/></svg>47 Automotive suppliers, NAFTA</p>
    <p style="margin-bottom:9px;margin-right:40px"><svg class="tick" viewBox="0 0 10 10"><circle cx="5" cy="5" r="5" fill="#fff"/><path d="M2.6 5.2 4.3 6.8 7.4 3.5" stroke="#1b2f6b" stroke-width="1.3" fill="none"/></svg>$3Billion dollar supplier base</p>
    <p style="text-align:left;margin-left:45px;padding-left:13px;text-indent:-13px"><svg class="tick" viewBox="0 0 10 10"><circle cx="5" cy="5" r="5" fill="#fff"/><path d="M2.6 5.2 4.3 6.8 7.4 3.5" stroke="#1b2f6b" stroke-width="1.3" fill="none"/></svg>$95Million dollar required annual cost reduction</p>
  </div>
  <p class="abs" style="left:190px;top:135px;width:205px;font-size:6.8px;line-height:8.5px;text-align:center">A supplier survey was created to identify actual cost reduction impact. The survey identified gaps between the cost reduction target and individual suppliers actual effort. A set of questions was created to help identify areas of impact, ability to implement cost reduction, and the capability to measure results.</p>
  <div class="page-no">3</div>
</section>

<!-- 4 Gap analysis -->
<section class="slide col-b row-2">
  <div class="abs photo-sparks" style="inset:0" role="img" aria-label="Photo of a welder with flying sparks"></div>
  <div class="panel" style="left:0;top:35px;width:409px;height:195px;clip-path:polygon(0 0,78% 0,60% 100%,0 100%)"></div>
  <div class="panel" style="left:0;top:35px;width:320px;height:195px"></div>
  <div class="header-band" style="width:270px;clip-path:polygon(0 0,100% 0,94% 100%,0 100%)"><span class="bar"></span>Supplier Survey, Gap Analysis</div>
  <p class="abs" style="left:12px;top:39px;width:210px;font-size:7px;line-height:8.5px">Reported areas of impact towards annual cost reduction requirements</p>
  <p class="abs" style="left:12px;top:66px;font-size:7px;line-height:9px">Categories:<br>-Raw material<br>-Machine process<br>-Assembly<br>-Components<br>-Packaging<br>-Tooling<br>-Quality<br><br>Impact:<br>-Energy<br>-Productivity</p>
  <svg class="abs grid-svg" style="left:88px;top:50px" width="225" height="170" viewBox="0 0 225 170">
    <rect width="225" height="170" fill="#fbfbfb"/>
    <rect width="225" height="6" fill="#1b2f6b"/>
    <g>
      <rect x="60" y="20" width="22" height="5" fill="var(--cell-red)"/><rect x="82" y="30" width="22" height="5" fill="var(--cell-orange)"/>
      <rect x="104" y="40" width="22" height="5" fill="var(--cell-green)"/><rect x="60" y="50" width="22" height="5" fill="var(--cell-yellow)"/>
      <rect x="126" y="55" width="22" height="5" fill="var(--cell-red)"/><rect x="82" y="65" width="22" height="5" fill="var(--cell-green)"/>
      <rect x="148" y="70" width="22" height="5" fill="var(--cell-orange)"/><rect x="104" y="80" width="22" height="5" fill="var(--cell-yellow)"/>
      <rect x="60" y="90" width="22" height="5" fill="var(--cell-orange)"/><rect x="170" y="95" width="22" height="5" fill="var(--cell-green)"/>
      <rect x="126" y="105" width="22" height="5" fill="var(--cell-yellow)"/><rect x="82" y="115" width="22" height="5" fill="var(--cell-red)"/>
      <rect x="148" y="120" width="22" height="5" fill="var(--cell-red)"/><rect x="60" y="130" width="22" height="5" fill="var(--cell-green)"/>
      <rect x="104" y="140" width="22" height="5" fill="var(--cell-orange)"/><rect x="192" y="60" width="22" height="5" fill="var(--cell-green)"/>
      <rect x="170" y="150" width="22" height="5" fill="var(--cell-yellow)"/><rect x="82" y="155" width="22" height="5" fill="var(--cell-orange)"/>
    </g>
    <g stroke="#e3e3e3" stroke-width=".4">
      <path d="M0 15H225M0 25H225M0 35H225M0 45H225M0 55H225M0 65H225M0 75H225M0 85H225M0 95H225M0 105H225M0 115H225M0 125H225M0 135H225M0 145H225M0 155H225M0 165H225"/>
      <path d="M20 6V170M38 6V170M60 6V170M82 6V170M104 6V170M126 6V170M148 6V170M170 6V170M192 6V170M214 6V170"/>
    </g>
    <rect y="164" width="225" height="6" fill="#1b2f6b"/>
  </svg>
  <div class="abs" style="left:320px;top:110px;width:85px;height:30px;background:rgba(19,34,90,.85);font-size:6.6px;line-height:8px;padding:3px 0 0 9px">Add legend with color <span style="color:#ff4a3a">red</span> to <span style="color:#5fd36a">green</span><br><span style="color:#ff4a3a">best</span> to <span style="color:#f7d64a">poor</span></div>
  <div class="page-no">4</div>
</section>

<!-- 5 Survey data -->
<section class="slide col-a row-3">
  <div class="abs photo-gears" style="inset:0" role="img" aria-label="Photo of steel industrial gears"></div>
  <div class="panel" style="left:45px;top:30px;width:364px;height:170px"></div>
  <div class="header-band" style="width:215px;clip-path:polygon(0 0,100% 0,88% 100%,0 100%)"><span class="bar"></span>Supplier Survey, Data</div>
  <svg class="abs grid-svg" style="left:56px;top:58px" width="150" height="94" viewBox="0 0 150 94">
    <rect width="150" height="94" fill="#fff"/>
    <rect width="150" height="12" fill="#c9d4ee"/>
    <text x="75" y="7" font-size="5.5" fill="#1b2f6b" text-anchor="middle">Areas of impact</text>
    <g font-size="2.8" fill="#1b2f6b" font-weight="700"><text x="5" y="11">Raw Material</text><text x="45" y="11">Machine process</text><text x="86" y="11">Assembly</text><text x="118" y="11">Components</text></g>
    <rect x="0" y="12" width="38" height="4" fill="var(--cell-orange)"/><rect x="38" y="12" width="38" height="4" fill="var(--cell-pale)"/>
    <rect x="38" y="21" width="38" height="4" fill="var(--cell-pale)"/>
    <rect x="76" y="30" width="38" height="4" fill="var(--cell-orange)"/><rect x="114" y="30" width="36" height="4" fill="var(--cell-orange)"/>
    <rect x="0" y="35" width="38" height="8" fill="var(--cell-red)"/><rect x="38" y="35" width="38" height="8" fill="var(--cell-yellow)"/><rect x="114" y="39" width="36" height="4" fill="var(--cell-green)"/>
    <rect x="76" y="44" width="38" height="8" fill="var(--cell-yellow)"/><rect x="114" y="44" width="36" height="8" fill="var(--cell-pale)"/>
    <rect x="0" y="48" width="38" height="4" fill="var(--cell-yellow)"/><rect x="38" y="48" width="38" height="4" fill="var(--cell-pale)"/>
    <rect x="38" y="52" width="76" height="8" fill="var(--cell-orange)"/>
    <rect x="0" y="64" width="38" height="8" fill="var(--cell-red)"/><rect x="76" y="64" width="38" height="16" fill="var(--cell-orange)"/>
    <rect x="38" y="72" width="38" height="4" fill="var(--cell-pale)"/><rect x="114" y="72" width="36" height="4" fill="var(--cell-yellow)"/>
    <g font-size="3" fill="#222">
      <text x="10" y="15">$5,000.00</text><text x="48" y="15">$10,000.00</text><text x="48" y="24">$13,410.00</text>
      <text x="86" y="33">$3,000.00</text><text x="124" y="33">$3,000.00</text>
      <text x="10" y="38">$3,740.00</text><text x="48" y="38">$3,740.00</text>
      <text x="10" y="42">$71,590.00</text><text x="48" y="42">$55,000.00</text><text x="124" y="42">$60,000.00</text>
      <text x="86" y="47">$5,000.00</text><text x="124" y="47">$6,000.00</text>
      <text x="10" y="51">$25,000.00</text><text x="48" y="51">$14,000.00</text><text x="86" y="51">$4,000.00</text><text x="124" y="51">$8,000.00</text>
      <text x="48" y="55">$600.00</text><text x="86" y="55">$2,200.00</text><text x="48" y="59">$3,000.00</text><text x="124" y="59">$3,000.00</text>
      <text x="10" y="67">$3,000.00</text><text x="86" y="67">$3,000.00</text>
      <text x="10" y="71">$5,000.00</text><text x="48" y="71">$13,000.00</text><text x="86" y="71">$2,500.00</text><text x="124" y="71">$20,000.00</text>
      <text x="86" y="75">$1,125.00</text>
    </g>
  </svg>
  <p class="abs" style="left:56px;top:154px;font-size:4px;line-height:5px"><span style="color:#ff4a3a">Red</span> – poor effort<br><span style="color:#5fd36a">Green</span> – best effort</p>
  <svg class="abs" style="left:220px;top:75px" width="180" height="70" viewBox="0 0 180 70">
    <g stroke="#fff" stroke-width=".8" fill="none">
      <path d="M24 33H14V56M14 33V20M14 33H22"/>
      <path d="M97 33H107M110 28V40M110 34H117"/>
      <circle cx="110" cy="28" r="1" fill="#fff"/><circle cx="110" cy="40" r="1" fill="#fff"/>
      <circle cx="14" cy="20" r="1" fill="#fff"/><circle cx="14" cy="56" r="1" fill="#fff"/>
    </g>
  </svg>
  <div class="abs" style="left:241px;top:82px;font-size:5.5px">Aptitude</div>
  <div class="node" style="left:244px;top:93px;width:50px;height:34px;line-height:6.5px">Capital<br>Technical<br>Resources<br>Event</div>
  <div class="abs" style="left:346px;top:90px;font-size:5.5px">Measure</div>
  <div class="node" style="left:338px;top:100px;width:42px;height:13px">Energy</div>
  <div class="node" style="left:338px;top:113px;width:42px;height:13px">Productivity</div>
  <p class="abs" style="right:30px;top:153px;width:200px;text-align:right;font-size:7px;line-height:8.5px">Minimal effort… <b>What is missing?</b><br>What separates <b>good vs poor effort?</b><br>Technical <b>know how?</b><br>Resources, <b>manpower?</b><br>An event, <b>the right timing?</b></p>
  <div class="page-no">5</div>
</section>

<!-- 6 Individual effort -->
<section class="slide col-b row-3">
  <div class="abs photo-sparks" style="inset:0" role="img" aria-label="Photo of metal grinding sparks"></div>
  <div class="panel" style="inset:0;clip-path:polygon(0 0,64% 0,30% 100%,0 100%)"></div>
  <div class="panel" style="inset:0;clip-path:polygon(80% 0,100% 0,100% 100%,60% 100%)"></div>
  <div class="abs" style="left:0;top:0;width:260px;height:42px;background:var(--navy-deep);clip-path:polygon(0 0,100% 0,90% 100%,0 100%)"></div>
  <span class="bar-light" style="left:3px;top:13px"></span>
  <div class="dark-title" style="top:4px;width:235px">Individual Supplier Effort is Not Enough</div>
  <svg class="abs" style="left:60px;top:80px" width="120" height="90" viewBox="0 0 120 90">
    <ellipse cx="50" cy="50" rx="46" ry="26" fill="#6f7380"/>
    <ellipse cx="50" cy="45" rx="46" ry="26" fill="#dcdde2"/>
    <path d="M62 38 L62 12 A46 26 0 0 1 98 30 Z" fill="#fff" stroke="#1b2f6b" stroke-width=".8"/>
    <path d="M40 55 L10 70" stroke="#fff" stroke-width=".7"/>
    <path d="M72 14 L84 4" stroke="#fff" stroke-width=".7"/>
  </svg>
  <div class="abs" style="left:157px;top:75px;font-size:11px;font-weight:700">$5.7M</div>
  <div class="abs" style="left:148px;top:89px;font-size:5.5px;line-height:6px;text-align:center;width:50px">Actual impact on cost reduction</div>
  <div class="abs" style="left:14px;top:147px;font-size:11px;font-weight:700">$96M</div>
  <div class="abs" style="left:14px;top:161px;font-size:5.5px;line-height:6px;width:40px;text-align:center">Required cost reduction</div>
  <div class="abs" style="left:268px;top:43px;width:33px;height:122px;background:#fff;color:#1b2f6b;font-size:4.5px;text-align:center;padding-top:50px;line-height:5px">Suppliers<br>Base<br>Condition</div>
  <div class="abs" style="left:327px;top:45px;width:1px;height:96px;background:#fff"></div>
  <div class="abs" style="left:312px;top:93px;font-size:4.8px;font-weight:700;line-height:5.5px;text-align:center;width:31px;background:var(--navy);padding:1px 0">▲% Cost Reduction Target</div>
  <div class="abs" style="left:312px;top:142px;width:31px;height:23px;background:#fff;color:#1b2f6b;font-size:4.5px;text-align:center;padding-top:4px;line-height:5px">Suppliers<br>Individual<br>effort</div>
  <div class="abs" style="left:60px;top:191px;width:216px;height:32px;background:rgba(210,213,222,.85);clip-path:polygon(5% 0,100% 0,95% 100%,0 100%);color:#1b2f6b;font-size:6.5px;text-align:center;padding:8px 18px 0;line-height:8px">Missed cost reduction targets, supplier accepts loss<br>and is forced to operate with lower margins</div>
</section>

<!-- 7 Innovative supplier cost reduction -->
<section class="slide col-a row-4">
  <div class="abs photo-gears" style="inset:0" role="img" aria-label="Photo of steel industrial gears"></div>
  <div class="panel" style="left:0;top:30px;width:409px;height:180px;clip-path:polygon(38% 0,100% 0,100% 100%,20% 100%)"></div>
  <div class="panel" style="left:120px;top:30px;width:289px;height:180px"></div>
  <div class="abs" style="left:0;top:0;width:225px;height:40px;background:var(--navy-deep);clip-path:polygon(0 0,100% 0,90% 100%,0 100%)"></div>
  <span class="bar-light" style="left:3px;top:15px"></span>
  <div class="dark-title" style="top:4px;width:200px">Innovative Supplier Cost Reduction</div>
  <p class="abs" style="right:28px;top:45px;width:240px;text-align:right;font-size:7px;line-height:9px">The goal is an alignment of innovative cost reduction technology and cost improvement requirements across the supplier group</p>
  <svg class="abs" style="left:182px;top:78px" width="120" height="100" viewBox="0 0 120 100">
    <path d="M4 10 C4 -2 116 -2 116 10 L72 72 L72 92 L48 92 L48 72 Z" fill="#c8cbd4" stroke="#fff"/>
    <circle cx="32" cy="28" r="16" fill="#fff"/><circle cx="84" cy="22" r="16" fill="#fff"/><circle cx="60" cy="58" r="15" fill="#fff"/>
    <g font-size="3" fill="#1b2f6b" text-anchor="middle"><text x="32" y="29">GAP Analysis</text><text x="84" y="23">Forecast data</text><text x="60" y="59">Requirements</text></g>
  </svg>
  <div class="pill" style="left:152px;top:163px;width:60px;text-align:center">Common Process</div>
  <div class="abs" style="left:213px;top:160px;font-size:18px;line-height:18px;font-weight:300">›</div>
  <div class="abs" style="left:286px;top:160px;font-size:18px;line-height:18px;font-weight:300">‹</div>
  <div class="pill" style="left:296px;top:163px;width:52px;text-align:center">Best Practices</div>
  <div class="abs" style="left:200px;top:187px;width:104px;text-align:center;font-size:7px">Immediate Innovation</div>
  <div class="abs" style="left:200px;top:200px;width:104px;text-align:center;font-size:5.5px">$ Cost Reduction</div>
  <div class="page-no">7</div>
</section>

<!-- 8 Collaborative effort -->
<section class="slide col-b row-4">
  <div class="abs photo-sparks" style="inset:0" role="img" aria-label="Photo of an industrial workshop"></div>
  <div class="panel" style="left:0;top:32px;width:409px;height:170px"></div>
  <div class="header-band" style="width:215px;clip-path:polygon(0 0,100% 0,92% 100%,0 100%)"><span class="bar"></span>Collaborative Effort</div>
  <div class="abs" style="left:82px;top:49px;font-size:8.8px;line-height:10.5px;width:320px;font-weight:400">
    <p style="margin-bottom:4px"><svg class="tick" viewBox="0 0 10 10"><circle cx="5" cy="5" r="5" fill="#fff"/><path d="M2.6 5.2 4.3 6.8 7.4 3.5" stroke="#1b2f6b" stroke-width="1.3" fill="none"/></svg>Leveraging the power of a $3B supplier base</p>
    <p style="margin-bottom:4px"><svg class="tick" viewBox="0 0 10 10"><circle cx="5" cy="5" r="5" fill="#fff"/><path d="M2.6 5.2 4.3 6.8 7.4 3.5" stroke="#1b2f6b" stroke-width="1.3" fill="none"/></svg>Identifying a healthy effort towards $95M cost reduction targets</p>
    <p style="padding-left:13px;text-indent:-13px"><svg class="tick" viewBox="0 0 10 10"><circle cx="5" cy="5" r="5" fill="#fff"/><path d="M2.6 5.2 4.3 6.8 7.4 3.5" stroke="#1b2f6b" stroke-width="1.3" fill="none"/></svg>Using the maximum group effort of $23M to influence cost reduction innovation</p>
  </div>
  <div class="quad">
    <div class="abs" style="left:125px;top:0;width:1px;height:72px;background:#fff"></div>
    <div class="abs" style="left:0;top:36px;width:249px;height:1px;background:#fff"></div>
    <span style="left:0;top:8px">Production Forecast</span>
    <span style="left:50%;top:8px">ROI Development</span>
    <span style="left:0;top:53px">Supplier Group Survey</span>
    <span style="left:50%;top:53px">New Model Events</span>
  </div>
  <div class="impact">Impact</div>
  <div class="page-no">8</div>
</section>

<!-- 9 Strength -->
<section class="slide col-a row-5">
  <div class="abs photo-sparks" style="inset:0" role="img" aria-label="Photo of a welder with sparks"></div>
  <div class="panel" style="left:0;top:32px;width:409px;height:198px;clip-path:polygon(0 0,60% 0,100% 60%,100% 100%,0 100%)"></div>
  <div class="panel" style="left:0;top:32px;width:300px;height:198px"></div>
  <div class="header-band" style="width:260px;clip-path:polygon(0 0,100% 0,94% 100%,0 100%)"><span class="bar"></span>Strength</div>
  <svg class="abs" style="left:0;top:0" width="409" height="230" viewBox="0 0 409 230">
    <circle cx="107" cy="99" r="26" fill="#2a3a9a" stroke="#fff" stroke-width="1"/>
    <circle cx="244" cy="85" r="40" fill="#2a3a9a" stroke="#fff" stroke-width="1"/>
    <path d="M107 125V136H244V125" stroke="#fff" stroke-width="2.2" fill="none"/>
    <path d="M173 137 L157 160 H189 Z" fill="none" stroke="#fff" stroke-width="2.2"/>
  </svg>
  <div class="center-label" style="left:107px;top:66px;font-size:7px">Max Effort</div>
  <div class="center-label" style="left:107px;top:99px;font-family:Montserrat,sans-serif;font-weight:700;font-size:12px">$23M</div>
  <div class="center-label" style="left:246px;top:40px;font-size:7px">Target</div>
  <div class="center-label" style="left:244px;top:85px;font-family:Montserrat,sans-serif;font-weight:700;font-size:19px">$96M</div>
  <div class="abs" style="left:140px;top:162px;width:70px;height:12px;background:#fff;color:#16204a;font-size:6.5px;font-weight:700;text-align:center;line-height:12px">$3B supplier base</div>
  <p class="abs" style="left:55px;top:182px;width:242px;text-align:center;font-size:6.8px;line-height:8.5px">Managing cost is more than mere price reduction. It is a longer term strategy and requires a more collaborative effort towards cost reduction.</p>
  <div class="page-no">9</div>
</section>

<!-- 10 Supplier collaborative effort -->
<section class="slide col-b row-5">
  <div class="abs photo-gears" style="inset:0" role="img" aria-label="Photo of steel industrial gears"></div>
  <div class="panel" style="left:80px;top:32px;width:329px;height:198px"></div>
  <div class="panel" style="left:0;top:32px;width:100px;height:198px;clip-path:polygon(0 0,100% 0,100% 100%,80% 100%,20% 30%,0 30%)"></div>
  <div class="header-band" style="width:222px;font-size:14.5px;clip-path:polygon(0 0,100% 0,92% 100%,0 100%)"><span class="bar"></span>Supplier Collaborative Effort</div>
  <div class="center-label" style="left:88px;top:120px;font-size:6.5px;transform:translate(-50%,-50%) rotate(-90deg)">Sustainable Cost &amp; Competitive Advantage</div>
  <svg class="abs" style="left:0;top:0" width="409" height="230" viewBox="0 0 409 230">
    <path d="M106 185 C118 135 165 75 300 67" stroke="#fff" stroke-width="4" fill="none"/>
    <path d="M298 57 L318 67 L298 77 Z" fill="#fff"/>
    <circle cx="106" cy="185" r="5" fill="var(--navy)" stroke="#fff" stroke-width="2"/>
    <circle cx="127" cy="141" r="4" fill="var(--navy)" stroke="#fff" stroke-width="1.5"/>
    <circle cx="166" cy="100" r="4" fill="var(--navy)" stroke="#fff" stroke-width="1.5"/>
    <circle cx="226" cy="72" r="4" fill="var(--navy)" stroke="#fff" stroke-width="1.5"/>
  </svg>
  <div class="abs nowrap" style="left:138px;top:138px;font-size:6.8px">Co-operation</div>
  <div class="abs nowrap" style="left:174px;top:102px;font-size:6.8px">Collaborative</div>
  <div class="abs nowrap" style="left:232px;top:74px;font-size:6.8px;text-align:center;line-height:8px">Immediate<br>innovation</div>
  <div class="abs nowrap" style="left:318px;top:78px;font-size:6.8px;text-align:center;line-height:8px">Assured cost<br>reductions</div>
  <div class="abs nowrap" style="left:155px;top:201px;font-size:6.8px">Collaborative cost reduction</div>
  <div class="page-no">10</div>
</section>

</body>
</html>
```